Whitcombe Business Card Design

The name of the business is Dario Whitcombe, CPA LLC
The service that we offer is Accounting, Tax & Consulting Services. I need it to have the following items:
Dario Whitcombe, Principal
Phone Number
Email Address
Physical Address

I have attached the company logo, one in black and one in white. Please provide a design in black background and the other in white background. Please include "Accounting, Tax & Consulting Services". I want the business card to be clean and very professional.

```html
<!DOCTYPE html>
<html lang="en">
<head>
<meta charset="utf-8">
<title>Dario Whitcombe, CPA LLC — Business Cards</title>
<link href="https://fonts.googleapis.com/css2?family=Montserrat:wght@400;500;600;700&family=Oswald:wght@500&display=swap" rel="stylesheet">
<style>
  :root {
    --stage: #56575a;
    --card-dark: #38383a;
    --card-light: #ffffff;
    --ink: #2e2e30;
    --grey-type: #8c8c8e;
    --accent: #a3151d;
    --on-dark: #e9e9ea;
    --on-dark-soft: #9a9a9c;
    --rule-grey: #9a9a9c;
  }
  * { box-sizing: border-box; margin: 0; padding: 0; }
  html, body { width: 1200px; height: 900px; overflow: hidden; }
  body {
    background: var(--stage);
    font-family: "Montserrat", sans-serif;
    position: relative;
  }
  .card {
    position: absolute;
    width: 560px;
    height: 320px;
    border-radius: 22px;
    overflow: hidden;
  }

  /* Front (dark) */
  .card-front {
    left: 60px; top: 80px;
    background: var(--card-dark);
    display: flex; flex-direction: column;
    align-items: center; justify-content: center;
    text-align: center;
  }
  .front-mark { display: flex; align-items: center; gap: 12px; }
  .front-mark .mark-square { width: 18px; height: 18px; background: var(--on-dark); }
  .front-name {
    font-weight: 600; font-size: 30px; color: var(--on-dark);
    letter-spacing: 0.5px;
  }
  .front-subline {
    margin-top: 8px;
    font-weight: 500; font-size: 15px; letter-spacing: 3px;
    text-transform: uppercase; color: var(--on-dark-soft);
  }
  .front-services {
    margin-top: 26px;
    font-size: 15px; color: #ffffff; letter-spacing: 0.3px;
  }

  /* Back (white) */
  .card-back {
    left: 580px; top: 490px;
    background: var(--card-light);
  }
  .back-brand { position: absolute; right: 24px; top: 44px; text-align: right; }
  .back-brand .brand-name {
    display: flex; align-items: center; justify-content: flex-end; gap: 8px;
    font-weight: 600; font-size: 18px; color: var(--ink);
  }
  .back-brand .mark-square { width: 10px; height: 10px; background: var(--ink); }
  .back-brand .brand-subline {
    margin-top: 3px;
    font-weight: 500; font-size: 9.5px; letter-spacing: 2px;
    text-transform: uppercase; color: var(--grey-type);
  }
  .brand-rule {
    position: absolute; left: 190px; right: 22px; top: 108px;
    height: 1px; background: var(--ink);
  }
  .holder { position: absolute; left: 30px; top: 132px; }
  .holder-name {
    font-weight: 700; font-size: 27px; color: var(--accent);
    text-transform: uppercase; letter-spacing: -0.3px; line-height: 1.2;
  }
  .holder-title { font-size: 15px; color: var(--ink); margin-top: 2px; }
  .contact-list { position: absolute; left: 30px; top: 200px; list-style: none; }
  .contact-list li {
    display: flex; align-items: center; gap: 12px;
    font-size: 14px; color: var(--ink); height: 24px;
  }
  .contact-list svg { width: 14px; height: 14px; fill: var(--accent); flex: none; }
  .address {
    position: absolute; right: 24px; top: 130px; text-align: right;
    font-style: normal; font-size: 14px; line-height: 1.45; color: var(--ink);
  }
  .back-bands { position: absolute; left: 0; bottom: 0; width: 560px; height: 80px; }
  .band-label {
    position: absolute; right: 18px; bottom: 31px;
    font-family: "Oswald", sans-serif; font-weight: 500;
    font-size: 12px; line-height: 1; letter-spacing: 0.5px; color: #ffffff;
    text-transform: uppercase; white-space: nowrap;
  }
</style>
</head>
<body>

  <section class="card card-front" aria-label="Card front">
    <div class="front-mark">
      <span class="mark-square"></span>
      <span class="front-name">Dario Whitcombe, CPA LLC</span>
    </div>
    <p class="front-subline">Certified Public Accountant</p>
    <p class="front-services">Accounting, Tax &amp; Consulting Services</p>
  </section>

  <section class="card card-back" aria-label="Card back">
    <div class="back-brand">
      <div class="brand-name"><span class="mark-square"></span>Dario Whitcombe, CPA LLC</div>
      <p class="brand-subline">Certified Public Accountant</p>
    </div>
    <div class="brand-rule"></div>

    <div class="holder">
      <h1 class="holder-name">Dario Whitcombe</h1>
      <p class="holder-title">Principal</p>
    </div>

    <ul class="contact-list">
      <li>
        <svg viewBox="0 0 24 24" aria-hidden="true"><path d="M6.6 10.8a15.1 15.1 0 0 0 6.6 6.6l2.2-2.2c.3-.3.7-.4 1-.2 1.1.4 2.3.6 3.6.6.6 0 1 .4 1 1V20c0 .6-.4 1-1 1A17 17 0 0 1 3 4c0-.6.4-1 1-1h3.5c.6 0 1 .4 1 1 0 1.3.2 2.5.6 3.6.1.3 0 .7-.2 1z"/></svg>
        044-555 218 904
      </li>
      <li>
        <svg viewBox="0 0 24 24" aria-hidden="true"><path d="M2 5h20v14H2zm2 2v.5l8 5 8-5V7l-8 5z"/></svg>
        hello@whitcombecpa.com
      </li>
      <li>
        <svg viewBox="0 0 24 24" aria-hidden="true"><path d="M12 2a10 10 0 1 0 0 20 10 10 0 0 0 0-20zm0 2c1 0 2.3 2 2.8 5H9.2C9.7 6 11 4 12 4zM4.3 11h3.8c0 .7 0 1.4.1 2H4.3a8 8 0 0 1 0-2zm5.8 0h3.8a13 13 0 0 1 0 2h-3.8a13 13 0 0 1 0-2zm5.8 0h3.8a8 8 0 0 1 0 2h-3.8l.1-2zM9.2 15h5.6c-.5 3-1.8 5-2.8 5s-2.3-2-2.8-5z"/></svg>
        www.whitcombecpa.com
      </li>
    </ul>

    <address class="address">
      88 Linden Row, Suite 4<br>
      Fairhaven, 45210
    </address>

    <svg class="back-bands" viewBox="0 0 560 80" aria-hidden="true">
      <polygon points="0,62 270,62 296,26 304,26 276,68 0,68" fill="var(--accent)"/>
      <rect x="0" y="73" width="560" height="2" fill="var(--rule-grey)"/>
      <polygon points="312,18 560,18 560,66 280,66" fill="var(--ink)"/>
    </svg>
    <span class="band-label">Accounting, Tax &amp; Consulting Services</span>
  </section>

</body>
</html>
```